Business Card Design for Technology Company

New business card design needed for technology company director.
Ideally, the design will fit the style and nature of the industry. We are a supplier of quality products and services, and we hope the design will give customers and suppliers this impression.

Target Market(s)

3D Printing Industry

Industry/Entity Type

Technology Equipment

Contact Information for Business Card

Name: Marcus Lin
Title: Director
Company address: Factory K4, 7B Harlowe Road, Springvale Victoria Australia 3150
Telephone: +61-3-8555 6413
Email: marcus.lin@vortalmake.com.au
Website: www.vortalmake.com.au

Requirements
Must have
• All information in business card details
• Company logo
• '3D Printers and 3D Print Filaments' at proper place
Nice to have
• Style to fit the industry
• Colour to fit logo

```html
<!DOCTYPE html>
<html lang="en">
<head>
<meta charset="utf-8">
<title>Vortalmake Business Card</title>
<link rel="stylesheet" href="https://fonts.googleapis.com/css2?family=Lato:wght@400;700&family=Michroma&display=swap">
<style>
  :root {
    --backdrop: #666666;
    --card-light: #ffffff;
    --card-dark: #000000;
    --accent: #f7a11a;
    --ink: #333333;
    --rule-top: #b9b9b9;
    --rule-bottom: #1d8fd1;
    --shadow: rgba(0, 0, 0, 0.45);
    --white: #ffffff;
  }
  html, body {
    margin: 0;
    padding: 0;
    width: 1200px;
    height: 900px;
    overflow: hidden;
    background: var(--backdrop);
  }
  .stage {
    position: relative;
    width: 1200px;
    height: 900px;
  }
  .card {
    position: absolute;
    top: 276px;
    width: 477px;
    height: 293px;
    box-shadow: 2px 3px 4px var(--shadow);
  }
  .card--front {
    left: 120px;
    background: var(--card-light);
    border-radius: 0 55px 0 55px;
  }
  .card--back {
    left: 620px;
    background: var(--card-dark);
    border-radius: 55px 0 55px 0;
  }
  .brand-mark {
    position: absolute;
    display: flex;
    flex-direction: column;
    align-items: center;
    font-family: "Lato", sans-serif;
    font-weight: 700;
  }
  .brand-mark__square {
    background: var(--accent);
  }
  .card--front .brand-mark {
    left: 62px;
    top: 82px;
    width: 135px;
    gap: 14px;
  }
  .card--front .brand-mark__square {
    width: 60px;
    height: 60px;
  }
  .card--front .brand-mark__name {
    color: var(--ink);
    font-size: 18px;
    letter-spacing: 0.5px;
  }
  .divider {
    position: absolute;
    left: 220px;
    top: 69px;
    width: 2px;
    height: 154px;
    background: linear-gradient(var(--rule-top), var(--rule-bottom));
  }
  .contact {
    position: absolute;
    left: 244px;
    top: 70px;
    font-family: "Lato", sans-serif;
    color: var(--ink);
    font-size: 14px;
    line-height: 17.5px;
  }
  .contact__name {
    font-family: "Michroma", sans-serif;
    font-weight: 400;
    color: var(--accent);
    font-size: 15px;
    line-height: 18px;
    letter-spacing: 0.3px;
    margin: 0;
    -webkit-text-stroke: 0.4px var(--accent);
  }
  .contact__title {
    margin: 0 0 6px;
  }
  .contact__list {
    list-style: none;
    margin: 0;
    padding: 0;
  }
  .contact__item {
    display: flex;
    align-items: center;
    gap: 4px;
  }
  .contact__icon {
    width: 11px;
    height: 11px;
    fill: var(--accent);
    flex: none;
  }
  .contact__address {
    margin: 7px 0 0 2px;
    font-style: normal;
  }
  .card--back .brand-mark {
    left: 0;
    right: 0;
    top: 50px;
  }
  .card--back .brand-mark__square {
    width: 100px;
    height: 100px;
  }
  .card--back .brand-mark__name {
    margin-top: 52px;
    color: var(--white);
    font-size: 25px;
    line-height: 26px;
    letter-spacing: 5px;
  }
  .brand-mark__tagline {
    margin-top: 6px;
    color: var(--white);
    font-size: 10px;
    line-height: 12px;
    letter-spacing: 2.5px;
  }
</style>
</head>
<body>
<main class="stage">
  <section class="card card--front" aria-label="Card front">
    <div class="brand-mark">
      <span class="brand-mark__square"></span>
      <span class="brand-mark__name">Vortalmake</span>
    </div>
    <span class="divider"></span>
    <div class="contact">
      <p class="contact__name">MARCUS LIN</p>
      <p class="contact__title">Director</p>
      <ul class="contact__list">
        <li class="contact__item">
          <svg class="contact__icon" viewBox="0 0 12 12" aria-hidden="true"><path d="M1 4c0-2 2-3 5-3s5 1 5 3l-2 .5-.5-1.5h-5L3 4.5zM3 6h6l1.5 5h-9z"/></svg>
          <span>+61-3-8555 6413</span>
        </li>
        <li class="contact__item">
          <svg class="contact__icon" viewBox="0 0 12 12" aria-hidden="true"><path d="M1 2.5h10v7H1z"/><path d="M1.5 3.2l4.5 3.4 4.5-3.4" fill="none" stroke="#fff" stroke-width="0.9"/></svg>
          <span>marcus.lin@vortalmake.com.au</span>
        </li>
        <li class="contact__item">
          <svg class="contact__icon" viewBox="0 0 12 12" aria-hidden="true"><circle cx="6" cy="6" r="5"/><path d="M4 3.5c1 .5 1.5 1.5.5 2.5M7.5 7c.5 1 1.5 1 2 .5" fill="none" stroke="#fff" stroke-width="1"/></svg>
          <span>www.vortalmake.com.au</span>
        </li>
      </ul>
      <address class="contact__address">Factory K4, 7B Harlowe Road,<br>Springvale Victoria<br>Australia 3150</address>
    </div>
  </section>

  <section class="card card--back" aria-label="Card back">
    <div class="brand-mark">
      <span class="brand-mark__square"></span>
      <span class="brand-mark__name">VORTALMAKE</span>
      <span class="brand-mark__tagline">3D PRINTERS AND 3D PRINT FILAMENTS</span>
    </div>
  </section>
</main>
</body>
</html>
```